Oriel Photography Business Card

I need a business card designed for a photography business based in Perth, Western Australia called Oriel Photography.

We specialise in wedding, event photography and portrait photography.

The business card must borrow the style of the attached logo.

The hex codes for the colours in the logo are:
#ED1D85 - Pink
#89C23E - Green
#37282F - Black

The name on the card will be:
Name: Tobrian
Phone: 0417395268
Website: www.orielphotography.example.com.au
Facebook: orielphotography

I am open and happy to accept creative concepts.

I’d like some space at the back for writing notes and appointment details.

```html
<!DOCTYPE html>
<html lang="en">
<head>
<meta charset="utf-8">
<title>Oriel Photography – Business Card</title>
<link rel="stylesheet" href="https://fonts.googleapis.com/css2?family=Josefin+Sans:wght@300;400&family=Open+Sans:wght@400;600&family=Advent+Pro:wght@300;400&display=swap">
<style>
  :root {
    --pink: #ED1D85;
    --green: #89C23E;
    --ink: #37282F;
    --paper: #FFFFFF;
    --backdrop: #E9E6E3;
    --rule: #1E1A1C;
  }
  * { box-sizing: border-box; margin: 0; padding: 0; }
  html, body { width: 1200px; height: 984px; overflow: hidden; }
  body { background: var(--backdrop); font-family: "Open Sans", sans-serif; color: var(--ink); position: relative; }

  .card {
    position: absolute; left: 170px; width: 860px; height: 430px;
    background: var(--paper); overflow: hidden;
    box-shadow: 0 6px 18px rgba(0,0,0,.18);
  }
  .card--front { top: 40px; }
  .card--back { top: 514px; }
  .card__shapes { position: absolute; inset: 0; width: 100%; height: 100%; }

  .tab-url {
    position: absolute; left: 34px; top: 12px;
    color: var(--paper); font-weight: 600; font-size: 16px; white-space: nowrap;
  }
  .brand-mark { position: absolute; border-radius: 50%; background: var(--pink); }
  .brand-name {
    position: absolute; font-family: "Josefin Sans", sans-serif; font-weight: 300;
    color: var(--ink); text-transform: uppercase; white-space: nowrap;
  }
  .card--front .brand-mark { left: 520px; top: 30px; width: 70px; height: 70px; }
  .card--front .brand-name { left: 420px; top: 118px; font-size: 15px; letter-spacing: .42em; }

  .person { position: absolute; left: 560px; top: 165px; text-align: left; }
  .person__name { font-family: "Advent Pro", sans-serif; font-weight: 400; font-size: 34px; color: var(--rule); line-height: 1; }
  .person__role { font-size: 12px; margin-top: 8px; margin-left: 12px; color: var(--ink); }

  .contact { position: absolute; left: 36px; top: 300px; list-style: none; font-size: 15px; color: var(--rule); }
  .contact li { display: flex; align-items: center; gap: 8px; height: 24px; }
  .contact .row { display: flex; gap: 36px; }
  .contact .row span { display: flex; align-items: center; gap: 8px; }
  .icon { width: 14px; height: 14px; flex: none; }
  .icon-square { width: 13px; height: 13px; background: var(--pink); flex: none; }

  .card--back .brand-mark { left: 375px; top: 40px; width: 110px; height: 110px; }
  .card--back .brand-name { left: 0; right: 0; top: 178px; text-align: center; font-size: 24px; letter-spacing: .42em; }
  .write-line { position: absolute; left: 60px; right: 70px; height: 2px; background: var(--rule); }
  .write-line--one { top: 262px; }
  .write-line--two { top: 328px; }
  .back-url {
    position: absolute; left: 240px; width: 380px; top: 388px; height: 40px;
    text-align: center; line-height: 40px; color: var(--paper); font-weight: 600; font-size: 18px; white-space: nowrap;
  }
</style>
</head>
<body>

<section class="card card--front" aria-label="Card front">
  <svg class="card__shapes" viewBox="0 0 860 430" aria-hidden="true">
    <rect x="0" y="0" width="860" height="14" fill="var(--pink)"/>
    <path d="M0 0 H390 C435 0 430 46 485 46 H0 Z" fill="var(--green)"/>
    <path d="M440 388 C560 388 570 290 650 282 C720 274 800 262 860 250 V388 Z" fill="var(--green)"/>
    <rect x="0" y="388" width="860" height="12" fill="var(--pink)"/>
    <rect x="0" y="400" width="860" height="30" fill="var(--green)"/>
  </svg>
  <div class="tab-url">www.orielphotography.example.com.au</div>
  <div class="brand-mark" role="img" aria-label="Oriel Photography mark"></div>
  <div class="brand-name">Oriel Photography</div>
  <div class="person">
    <div class="person__name">Tobrian</div>
    <div class="person__role">CEO &amp; Founder</div>
  </div>
  <ul class="contact">
    <li>
      <svg class="icon" viewBox="0 0 14 14" aria-hidden="true"><path d="M7 1 C4 1 2.5 3 2.5 5.2 C2.5 8 7 13 7 13 C7 13 11.5 8 11.5 5.2 C11.5 3 10 1 7 1 Z" fill="var(--pink)"/><circle cx="7" cy="5.2" r="1.7" fill="#fff"/></svg>
      Unit 4, 18 Lantern Street, Northbridge WA 6003
    </li>
    <li class="row">
      <span>
        <svg class="icon" viewBox="0 0 14 14" aria-hidden="true"><path d="M3 1 L5.5 1 L6.5 4 L5 5.3 C5.8 7 7 8.2 8.7 9 L10 7.5 L13 8.5 L13 11 C13 12 12 13 11 13 C5.5 12.6 1.4 8.5 1 3 C1 2 2 1 3 1 Z" fill="var(--pink)"/></svg>
        0417395268
      </span>
      <span>
        <svg class="icon" viewBox="0 0 14 14" aria-hidden="true"><rect x="1" y="3" width="12" height="8" fill="var(--pink)"/><path d="M1 3 L7 8 L13 3" fill="none" stroke="#fff" stroke-width="1.2"/></svg>
        www.orielphotography.example.com.au
      </span>
    </li>
    <li><span class="icon-square"></span>orielphotography</li>
  </ul>
</section>

<section class="card card--back" aria-label="Card back">
  <svg class="card__shapes" viewBox="0 0 860 430" aria-hidden="true">
    <rect x="0" y="0" width="860" height="14" fill="var(--pink)"/>
    <path d="M0 362 C120 350 180 370 230 400 C300 430 560 430 630 400 C680 370 750 340 860 352 V430 H0 Z" fill="var(--green)"/>
    <rect x="240" y="388" width="380" height="40" rx="20" fill="var(--pink)"/>
  </svg>
  <div class="brand-mark" role="img" aria-label="Oriel Photography mark"></div>
  <div class="brand-name">Oriel Photography</div>
  <div class="write-line write-line--one"></div>
  <div class="write-line write-line--two"></div>
  <div class="back-url">www.orielphotography.example.com.au</div>
</section>

</body>
</html>
```